Fun A1 2012 family planner using clever typography and block colour

I have been looking for an A1 2012 family planner and I have not been able to find one. Hence I would like help to develop such a planner. I plan to print it on matt paper, portrait orientated. I have attached some reference pictures of our 2011 planner. I like interesting typography, clear clean colours and simple illustration. I need space to write in daily events and need the weeks and days to be clearly delineated from each other. Each day cell needs the date and day in it (please refer to the file uploaded for a visual reference confirming this). Each weekend needs some kind of colour/ typographic delineation. I want a design for a year-at-a-view calendar. I plan to print the planner in Sydney, Australia with brightloomprints.com.au and probably to sell printed copies online. The terms & conditions of this project are that I will own the design concept 100% and in perpetuity worldwide once payment has been made. (NB. The attached Work File in Word contains a rough layout and all months, days and dates all typed up to make for quicker design.)

Target Market(s)

Reasonably well heeled family of 4. 2 parents. 2 kids. 2 pets.

Industry/Entity Type

Events

Requirements
Must have
• The calendar must be portrait (not landscape orientated), A1 size. It will be printed on matt paper by brightloomprints.com.au. It must have months running left to right (Jan-Dec) and day/date cells running top to bottom (refer 2011 planner photos in file uploaded). The day/ date cells must be around 3(w)x2(h)cm - big enough to write daily events in. Weekends must be colour/ typographically delineated. 2012 year must be noted as must "A Pebblegate Inc Project" and web address in fine print bottom left hand left hand corner.
Nice to have
• A Pebblegate Inc logo in bottom left hand corder (perhaps Nimble Owl like: http://www.artmarketly.com/design_submission.aspx?designid=731462). Header/Footer space for customisation (e.g. "Hartono-Quist 2012 Planner" or "XYZ Co 2012 Planner".
Should not have
• The calendar should not use photographs or resemble standard or cheesy wall calendars. No watermarks please.

```html
<!DOCTYPE html>
<html lang="en">
<head>
<meta charset="utf-8">
<title>2012 Year Planner</title>
<link rel="stylesheet" href="https://fonts.googleapis.com/css2?family=Lobster&family=Roboto+Condensed:wght@300;400&family=Roboto:wght@900&display=swap">
<style>
:root{
  --jan:#f7a11a;--feb:#5f67ad;--mar:#e61e25;--apr:#12934a;--may:#d3501f;--jun:#e8192c;
  --jul:#0b4a2a;--aug:#fff200;--sep:#3ab54a;--oct:#ec0f6e;--nov:#2b3990;--dec:#1fb077;
  --rule:#d4d4d4;--ink:#8a8a8a;--paper:#ffffff;
}
*{margin:0;padding:0;box-sizing:border-box}
html,body{width:849px;height:1200px;overflow:hidden;background:var(--paper)}
.planner{position:relative;width:849px;height:1200px;background:radial-gradient(ellipse at 50% 50%,#ffffff 40%,#f3f3f3 100%)}
.month-bar{position:absolute;left:32px;top:64px;width:780px;display:grid;grid-template-columns:repeat(12,60px);column-gap:5px}
.month-name{height:59px;display:flex;align-items:center;justify-content:center;font-family:"Lobster",cursive;font-size:26px;color:#fff;-webkit-text-stroke:1.2px #111;text-shadow:1px 1px 0 #111;background:var(--c)}
.grid{position:absolute;left:32px;top:146px;width:780px;display:grid;grid-template-columns:repeat(12,65px)}
.month{list-style:none;border-right:1px solid #e2e2e2}
.month:last-child{border-right:0}
.month li{height:28.8px;border-bottom:1px solid var(--rule);position:relative}
.month li span{position:absolute;left:4px;top:4px;width:18px;height:20px;padding:1px 0 0 2px;font-family:"Roboto Condensed",sans-serif;font-weight:300;font-size:10px;line-height:10px;color:var(--ink)}
.month li small{display:block;font-size:4.6px;line-height:6px;letter-spacing:.1px}
.month li.weekend span{background:var(--c);color:#fff}
.m-aug li.weekend span{color:#fffbb0}
.footer{position:absolute;left:57px;top:1108px}
.year{font-family:"Roboto",sans-serif;font-weight:900;font-size:34px;letter-spacing:-1px;color:#fff;-webkit-text-stroke:1.4px #111;line-height:34px}
.credit{font-family:"Roboto Condensed",sans-serif;font-size:9px;letter-spacing:-.3px;color:#222}
</style>
</head>
<body>
<main class="planner">
<header class="month-bar">
  <div class="month-name" style="--c:var(--jan)">Jan</div>
  <div class="month-name" style="--c:var(--feb)">Feb</div>
  <div class="month-name" style="--c:var(--mar)">Mar</div>
  <div class="month-name" style="--c:var(--apr)">Apr</div>
  <div class="month-name" style="--c:var(--may)">May</div>
  <div class="month-name" style="--c:var(--jun)">Jun</div>
  <div class="month-name" style="--c:var(--jul)">Jul</div>
  <div class="month-name" style="--c:var(--aug)">Aug</div>
  <div class="month-name" style="--c:var(--sep)">Sep</div>
  <div class="month-name" style="--c:var(--oct)">Oct</div>
  <div class="month-name" style="--c:var(--nov)">Nov</div>
  <div class="month-name" style="--c:var(--dec)">Dec</div>
</header>

<section class="grid">
<ol class="month m-jan" style="--c:var(--jan)">
<li class="weekend"><span>01<small>SUN</small></span></li><li><span>02<small>MON</small></span></li><li><span>03<small>TUE</small></span></li><li><span>04<small>WED</small></span></li><li><span>05<small>THU</small></span></li><li><span>06<small>FRI</small></span></li><li class="weekend"><span>07<small>SAT</small></span></li><li class="weekend"><span>08<small>SUN</small></span></li><li><span>09<small>MON</small></span></li><li><span>10<small>TUE</small></span></li><li><span>11<small>WED</small></span></li><li><span>12<small>THU</small></span></li><li><span>13<small>FRI</small></span></li><li class="weekend"><span>14<small>SAT</small></span></li><li class="weekend"><span>15<small>SUN</small></span></li><li><span>16<small>MON</small></span></li><li><span>17<small>TUE</small></span></li><li><span>18<small>WED</small></span></li><li><span>19<small>THU</small></span></li><li><span>20<small>FRI</small></span></li><li class="weekend"><span>21<small>SAT</small></span></li><li class="weekend"><span>22<small>SUN</small></span></li><li><span>23<small>MON</small></span></li><li><span>24<small>TUE</small></span></li><li><span>25<small>WED</small></span></li><li><span>26<small>THU</small></span></li><li><span>27<small>FRI</small></span></li><li class="weekend"><span>28<small>SAT</small></span></li><li class="weekend"><span>29<small>SUN</small></span></li><li><span>30<small>MON</small></span></li><li><span>31<small>TUE</small></span></li>
</ol>
<ol class="month m-feb" style="--c:var(--feb)">
<li><span>01<small>WED</small></span></li><li><span>02<small>THU</small></span></li><li><span>03<small>FRI</small></span></li><li class="weekend"><span>04<small>SAT</small></span></li><li class="weekend"><span>05<small>SUN</small></span></li><li><span>06<small>MON</small></span></li><li><span>07<small>TUE</small></span></li><li><span>08<small>WED</small></span></li><li><span>09<small>THU</small></span></li><li><span>10<small>FRI</small></span></li><li class="weekend"><span>11<small>SAT</small></span></li><li class="weekend"><span>12<small>SUN</small></span></li><li><span>13<small>MON</small></span></li><li><span>14<small>TUE</small></span></li><li><span>15<small>WED</small></span></li><li><span>16<small>THU</small></span></li><li><span>17<small>FRI</small></span></li><li class="weekend"><span>18<small>SAT</small></span></li><li class="weekend"><span>19<small>SUN</small></span></li><li><span>20<small>MON</small></span></li><li><span>21<small>TUE</small></span></li><li><span>22<small>WED</small></span></li><li><span>23<small>THU</small></span></li><li><span>24<small>FRI</small></span></li><li class="weekend"><span>25<small>SAT</small></span></li><li class="weekend"><span>26<small>SUN</small></span></li><li><span>27<small>MON</small></span></li><li><span>28<small>TUE</small></span></li><li><span>29<small>WED</small></span></li><li></li><li></li>
</ol>
<ol class="month m-mar" style="--c:var(--mar)">
<li><span>01<small>THU</small></span></li><li><span>02<small>FRI</small></span></li><li class="weekend"><span>03<small>SAT</small></span></li><li class="weekend"><span>04<small>SUN</small></span></li><li><span>05<small>MON</small></span></li><li><span>06<small>TUE</small></span></li><li><span>07<small>WED</small></span></li><li><span>08<small>THU</small></span></li><li><span>09<small>FRI</small></span></li><li class="weekend"><span>10<small>SAT</small></span></li><li class="weekend"><span>11<small>SUN</small></span></li><li><span>12<small>MON</small></span></li><li><span>13<small>TUE</small></span></li><li><span>14<small>WED</small></span></li><li><span>15<small>THU</small></span></li><li><span>16<small>FRI</small></span></li><li class="weekend"><span>17<small>SAT</small></span></li><li class="weekend"><span>18<small>SUN</small></span></li><li><span>19<small>MON</small></span></li><li><span>20<small>TUE</small></span></li><li><span>21<small>WED</small></span></li><li><span>22<small>THU</small></span></li><li><span>23<small>FRI</small></span></li><li class="weekend"><span>24<small>SAT</small></span></li><li class="weekend"><span>25<small>SUN</small></span></li><li><span>26<small>MON</small></span></li><li><span>27<small>TUE</small></span></li><li><span>28<small>WED</small></span></li><li><span>29<small>THU</small></span></li><li><span>30<small>FRI</small></span></li><li class="weekend"><span>31<small>SAT</small></span></li>
</ol>
<ol class="month m-apr" style="--c:var(--apr)">
<li class="weekend"><span>01<small>SUN</small></span></li><li><span>02<small>MON</small></span></li><li><span>03<small>TUE</small></span></li><li><span>04<small>WED</small></span></li><li><span>05<small>THU</small></span></li><li><span>06<small>FRI</small></span></li><li class="weekend"><span>07<small>SAT</small></span></li><li class="weekend"><span>08<small>SUN</small></span></li><li><span>09<small>MON</small></span></li><li><span>10<small>TUE</small></span></li><li><span>11<small>WED</small></span></li><li><span>12<small>THU</small></span></li><li><span>13<small>FRI</small></span></li><li class="weekend"><span>14<small>SAT</small></span></li><li class="weekend"><span>15<small>SUN</small></span></li><li><span>16<small>MON</small></span></li><li><span>17<small>TUE</small></span></li><li><span>18<small>WED</small></span></li><li><span>19<small>THU</small></span></li><li><span>20<small>FRI</small></span></li><li class="weekend"><span>21<small>SAT</small></span></li><li class="weekend"><span>22<small>SUN</small></span></li><li><span>23<small>MON</small></span></li><li><span>24<small>TUE</small></span></li><li><span>25<small>WED</small></span></li><li><span>26<small>THU</small></span></li><li><span>27<small>FRI</small></span></li><li class="weekend"><span>28<small>SAT</small></span></li><li class="weekend"><span>29<small>SUN</small></span></li><li><span>30<small>MON</small></span></li><li></li>
</ol>
<ol class="month m-may" style="--c:var(--may)">
<li><span>01<small>TUE</small></span></li><li><span>02<small>WED</small></span></li><li><span>03<small>THU</small></span></li><li><span>04<small>FRI</small></span></li><li class="weekend"><span>05<small>SAT</small></span></li><li class="weekend"><span>06<small>SUN</small></span></li><li><span>07<small>MON</small></span></li><li><span>08<small>TUE</small></span></li><li><span>09<small>WED</small></span></li><li><span>10<small>THU</small></span></li><li><span>11<small>FRI</small></span></li><li class="weekend"><span>12<small>SAT</small></span></li><li class="weekend"><span>13<small>SUN</small></span></li><li><span>14<small>MON</small></span></li><li><span>15<small>TUE</small></span></li><li><span>16<small>WED</small></span></li><li><span>17<small>THU</small></span></li><li><span>18<small>FRI</small></span></li><li class="weekend"><span>19<small>SAT</small></span></li><li class="weekend"><span>20<small>SUN</small></span></li><li><span>21<small>MON</small></span></li><li><span>22<small>TUE</small></span></li><li><span>23<small>WED</small></span></li><li><span>24<small>THU</small></span></li><li><span>25<small>FRI</small></span></li><li class="weekend"><span>26<small>SAT</small></span></li><li class="weekend"><span>27<small>SUN</small></span></li><li><span>28<small>MON</small></span></li><li><span>29<small>TUE</small></span></li><li><span>30<small>WED</small></span></li><li><span>31<small>THU</small></span></li>
</ol>
<ol class="month m-jun" style="--c:var(--jun)">
<li><span>01<small>FRI</small></span></li><li class="weekend"><span>02<small>SAT</small></span></li><li class="weekend"><span>03<small>SUN</small></span></li><li><span>04<small>MON</small></span></li><li><span>05<small>TUE</small></span></li><li><span>06<small>WED</small></span></li><li><span>07<small>THU</small></span></li><li><span>08<small>FRI</small></span></li><li class="weekend"><span>09<small>SAT</small></span></li><li class="weekend"><span>10<small>SUN</small></span></li><li><span>11<small>MON</small></span></li><li><span>12<small>TUE</small></span></li><li><span>13<small>WED</small></span></li><li><span>14<small>THU</small></span></li><li><span>15<small>FRI</small></span></li><li class="weekend"><span>16<small>SAT</small></span></li><li class="weekend"><span>17<small>SUN</small></span></li><li><span>18<small>MON</small></span></li><li><span>19<small>TUE</small></span></li><li><span>20<small>WED</small></span></li><li><span>21<small>THU</small></span></li><li><span>22<small>FRI</small></span></li><li class="weekend"><span>23<small>SAT</small></span></li><li class="weekend"><span>24<small>SUN</small></span></li><li><span>25<small>MON</small></span></li><li><span>26<small>TUE</small></span></li><li><span>27<small>WED</small></span></li><li><span>28<small>THU</small></span></li><li><span>29<small>FRI</small></span></li><li class="weekend"><span>30<small>SAT</small></span></li><li></li>
</ol>
<ol class="month m-jul" style="--c:var(--jul)">
<li class="weekend"><span>01<small>SUN</small></span></li><li><span>02<small>MON</small></span></li><li><span>03<small>TUE</small></span></li><li><span>04<small>WED</small></span></li><li><span>05<small>THU</small></span></li><li><span>06<small>FRI</small></span></li><li class="weekend"><span>07<small>SAT</small></span></li><li class="weekend"><span>08<small>SUN</small></span></li><li><span>09<small>MON</small></span></li><li><span>10<small>TUE</small></span></li><li><span>11<small>WED</small></span></li><li><span>12<small>THU</small></span></li><li><span>13<small>FRI</small></span></li><li class="weekend"><span>14<small>SAT</small></span></li><li class="weekend"><span>15<small>SUN</small></span></li><li><span>16<small>MON</small></span></li><li><span>17<small>TUE</small></span></li><li><span>18<small>WED</small></span></li><li><span>19<small>THU</small></span></li><li><span>20<small>FRI</small></span></li><li class="weekend"><span>21<small>SAT</small></span></li><li class="weekend"><span>22<small>SUN</small></span></li><li><span>23<small>MON</small></span></li><li><span>24<small>TUE</small></span></li><li><span>25<small>WED</small></span></li><li><span>26<small>THU</small></span></li><li><span>27<small>FRI</small></span></li><li class="weekend"><span>28<small>SAT</small></span></li><li class="weekend"><span>29<small>SUN</small></span></li><li><span>30<small>MON</small></span></li><li><span>31<small>TUE</small></span></li>
</ol>
<ol class="month m-aug" style="--c:var(--aug)">
<li><span>01<small>WED</small></span></li><li><span>02<small>THU</small></span></li><li><span>03<small>FRI</small></span></li><li class="weekend"><span>04<small>SAT</small></span></li><li class="weekend"><span>05<small>SUN</small></span></li><li><span>06<small>MON</small></span></li><li><span>07<small>TUE</small></span></li><li><span>08<small>WED</small></span></li><li><span>09<small>THU</small></span></li><li><span>10<small>FRI</small></span></li><li class="weekend"><span>11<small>SAT</small></span></li><li class="weekend"><span>12<small>SUN</small></span></li><li><span>13<small>MON</small></span></li><li><span>14<small>TUE</small></span></li><li><span>15<small>WED</small></span></li><li><span>16<small>THU</small></span></li><li><span>17<small>FRI</small></span></li><li class="weekend"><span>18<small>SAT</small></span></li><li class="weekend"><span>19<small>SUN</small></span></li><li><span>20<small>MON</small></span></li><li><span>21<small>TUE</small></span></li><li><span>22<small>WED</small></span></li><li><span>23<small>THU</small></span></li><li><span>24<small>FRI</small></span></li><li class="weekend"><span>25<small>SAT</small></span></li><li class="weekend"><span>26<small>SUN</small></span></li><li><span>27<small>MON</small></span></li><li><span>28<small>TUE</small></span></li><li><span>29<small>WED</small></span></li><li><span>30<small>THU</small></span></li><li><span>31<small>FRI</small></span></li>
</ol>
<ol class="month m-sep" style="--c:var(--sep)">
<li class="weekend"><span>01<small>SAT</small></span></li><li class="weekend"><span>02<small>SUN</small></span></li><li><span>03<small>MON</small></span></li><li><span>04<small>TUE</small></span></li><li><span>05<small>WED</small></span></li><li><span>06<small>THU</small></span></li><li><span>07<small>FRI</small></span></li><li class="weekend"><span>08<small>SAT</small></span></li><li class="weekend"><span>09<small>SUN</small></span></li><li><span>10<small>MON</small></span></li><li><span>11<small>TUE</small></span></li><li><span>12<small>WED</small></span></li><li><span>13<small>THU</small></span></li><li><span>14<small>FRI</small></span></li><li class="weekend"><span>15<small>SAT</small></span></li><li class="weekend"><span>16<small>SUN</small></span></li><li><span>17<small>MON</small></span></li><li><span>18<small>TUE</small></span></li><li><span>19<small>WED</small></span></li><li><span>20<small>THU</small></span></li><li><span>21<small>FRI</small></span></li><li class="weekend"><span>22<small>SAT</small></span></li><li class="weekend"><span>23<small>SUN</small></span></li><li><span>24<small>MON</small></span></li><li><span>25<small>TUE</small></span></li><li><span>26<small>WED</small></span></li><li><span>27<small>THU</small></span></li><li><span>28<small>FRI</small></span></li><li class="weekend"><span>29<small>SAT</small></span></li><li class="weekend"><span>30<small>SUN</small></span></li><li></li>
</ol>
<ol class="month m-oct" style="--c:var(--oct)">
<li><span>01<small>MON</small></span></li><li><span>02<small>TUE</small></span></li><li><span>03<small>WED</small></span></li><li><span>04<small>THU</small></span></li><li><span>05<small>FRI</small></span></li><li class="weekend"><span>06<small>SAT</small></span></li><li class="weekend"><span>07<small>SUN</small></span></li><li><span>08<small>MON</small></span></li><li><span>09<small>TUE</small></span></li><li><span>10<small>WED</small></span></li><li><span>11<small>THU</small></span></li><li><span>12<small>FRI</small></span></li><li class="weekend"><span>13<small>SAT</small></span></li><li class="weekend"><span>14<small>SUN</small></span></li><li><span>15<small>MON</small></span></li><li><span>16<small>TUE</small></span></li><li><span>17<small>WED</small></span></li><li><span>18<small>THU</small></span></li><li><span>19<small>FRI</small></span></li><li class="weekend"><span>20<small>SAT</small></span></li><li class="weekend"><span>21<small>SUN</small></span></li><li><span>22<small>MON</small></span></li><li><span>23<small>TUE</small></span></li><li><span>24<small>WED</small></span></li><li><span>25<small>THU</small></span></li><li><span>26<small>FRI</small></span></li><li class="weekend"><span>27<small>SAT</small></span></li><li class="weekend"><span>28<small>SUN</small></span></li><li><span>29<small>MON</small></span></li><li><span>30<small>TUE</small></span></li><li><span>31<small>WED</small></span></li>
</ol>
<ol class="month m-nov" style="--c:var(--nov)">
<li><span>01<small>THU</small></span></li><li><span>02<small>FRI</small></span></li><li class="weekend"><span>03<small>SAT</small></span></li><li class="weekend"><span>04<small>SUN</small></span></li><li><span>05<small>MON</small></span></li><li><span>06<small>TUE</small></span></li><li><span>07<small>WED</small></span></li><li><span>08<small>THU</small></span></li><li><span>09<small>FRI</small></span></li><li class="weekend"><span>10<small>SAT</small></span></li><li class="weekend"><span>11<small>SUN</small></span></li><li><span>12<small>MON</small></span></li><li><span>13<small>TUE</small></span></li><li><span>14<small>WED</small></span></li><li><span>15<small>THU</small></span></li><li><span>16<small>FRI</small></span></li><li class="weekend"><span>17<small>SAT</small></span></li><li class="weekend"><span>18<small>SUN</small></span></li><li><span>19<small>MON</small></span></li><li><span>20<small>TUE</small></span></li><li><span>21<small>WED</small></span></li><li><span>22<small>THU</small></span></li><li><span>23<small>FRI</small></span></li><li class="weekend"><span>24<small>SAT</small></span></li><li class="weekend"><span>25<small>SUN</small></span></li><li><span>26<small>MON</small></span></li><li><span>27<small>TUE</small></span></li><li><span>28<small>WED</small></span></li><li><span>29<small>THU</small></span></li><li><span>30<small>FRI</small></span></li><li></li>
</ol>
<ol class="month m-dec" style="--c:var(--dec)">
<li class="weekend"><span>01<small>SAT</small></span></li><li class="weekend"><span>02<small>SUN</small></span></li><li><span>03<small>MON</small></span></li><li><span>04<small>TUE</small></span></li><li><span>05<small>WED</small></span></li><li><span>06<small>THU</small></span></li><li><span>07<small>FRI</small></span></li><li class="weekend"><span>08<small>SAT</small></span></li><li class="weekend"><span>09<small>SUN</small></span></li><li><span>10<small>MON</small></span></li><li><span>11<small>TUE</small></span></li><li><span>12<small>WED</small></span></li><li><span>13<small>THU</small></span></li><li><span>14<small>FRI</small></span></li><li class="weekend"><span>15<small>SAT</small></span></li><li class="weekend"><span>16<small>SUN</small></span></li><li><span>17<small>MON</small></span></li><li><span>18<small>TUE</small></span></li><li><span>19<small>WED</small></span></li><li><span>20<small>THU</small></span></li><li><span>21<small>FRI</small></span></li><li class="weekend"><span>22<small>SAT</small></span></li><li class="weekend"><span>23<small>SUN</small></span></li><li><span>24<small>MON</small></span></li><li><span>25<small>TUE</small></span></li><li><span>26<small>WED</small></span></li><li><span>27<small>THU</small></span></li><li><span>28<small>FRI</small></span></li><li class="weekend"><span>29<small>SAT</small></span></li><li class="weekend"><span>30<small>SUN</small></span></li><li><span>31<small>MON</small></span></li>
</ol>
</section>

<footer class="footer">
  <div class="year">2012</div>
  <div class="credit">A Pebblegate Inc Project</div>
</footer>
</main>
</body>
</html>
```